Kestrelbrook Student Accomodation needs a business card design

Hi Guys,

We are a Student Accommodation company in Australia. We already have a logo which I will submit.

I will require the design of the business cards from you.

I am after something that looks clean, modern and that people feel interested and actually want to contact us.

We would like to see designs that are innovative.

On the business cards I will require to have:

Employee Name
Position
Phone number
Email
Facebook page

I hope you can help me with this project guys as I have heard really good things from you.

```html
<!DOCTYPE html>
<html lang="en">
<head>
<meta charset="utf-8">
<title>Kestrelbrook Student Accomodation — Business Card</title>
<link rel="stylesheet" href="https://fonts.googleapis.com/css2?family=Lato:wght@300;400;700&display=swap">
<style>
  :root {
    --page-bg: #d9d9d9;
    --card-green: #0f8d45;
    --card-black: #050505;
    --ink-white: #ffffff;
    --ink-grey: #6b6b6b;
    --url-grey: #8c8c8c;
    --brand-yellow: #f2b632;
    --brand-grey: #5a5a5a;
  }
  * { margin: 0; padding: 0; box-sizing: border-box; }
  html, body {
    width: 1200px; height: 926px; overflow: hidden;
    background: var(--page-bg);
    font-family: "Lato", sans-serif;
  }
  .sheet {
    width: 1200px; height: 926px;
    display: flex; flex-direction: column;
    align-items: center; justify-content: center; gap: 40px;
  }
  .card {
    position: relative;
    width: 700px; height: 400px;
    box-shadow: 0 6px 18px rgba(0,0,0,0.18);
  }
  /* Front */
  .card-front { background: var(--card-green); color: var(--ink-white); }
  .front-brand {
    position: absolute; left: 60px; top: 150px; width: 230px;
    display: flex; align-items: center; gap: 12px;
  }
  .brand-square { width: 22px; height: 22px; flex: none; }
  .front-brand .brand-square { background: var(--brand-grey); }
  .brand-name {
    font-weight: 700; font-size: 20px; line-height: 1.15;
    text-transform: uppercase; letter-spacing: 0.5px;
  }
  .front-brand .brand-name { color: var(--brand-grey); }
  .contact-block { position: absolute; left: 330px; top: 82px; }
  .person-name { font-size: 38px; font-weight: 300; line-height: 1; }
  .person-name strong { font-weight: 700; }
  .person-title { font-size: 11px; letter-spacing: 0.6px; margin-top: 6px; text-transform: uppercase; }
  .contact-list { list-style: none; margin-top: 34px; font-size: 17px; line-height: 1.45; }
  .contact-list li { display: flex; align-items: flex-start; gap: 10px; }
  .contact-list svg { width: 13px; height: 13px; flex: none; margin-top: 5px; fill: var(--ink-white); }
  .contact-list .address { margin-top: 4px; }
  /* Back */
  .card-back { background: var(--card-black); }
  .back-brand {
    position: absolute; left: 50%; top: 120px; transform: translateX(-50%);
    display: flex; align-items: center; gap: 14px; width: 320px;
  }
  .back-brand .brand-square { background: var(--brand-yellow); }
  .back-brand .brand-name { color: var(--brand-yellow); font-size: 22px; }
  .facebook-url {
    position: absolute; left: 60px; right: 40px; top: 250px;
    color: var(--url-grey); font-size: 16px; letter-spacing: 0.4px;
  }
</style>
</head>
<body>
<main class="sheet">
  <section class="card card-front" aria-label="Card front">
    <div class="front-brand">
      <span class="brand-square"></span>
      <span class="brand-name">Kestrelbrook Student Accomodation</span>
    </div>
    <div class="contact-block">
      <h1 class="person-name">John <strong>Smith</strong></h1>
      <p class="person-title">Title goes here</p>
      <ul class="contact-list">
        <li><svg viewBox="0 0 16 16" aria-hidden="true"><path d="M3 1l3 3-2 2c1 2 3 4 6 6l2-2 3 3-2 2C7 15 1 9 1 3z"/></svg>123-456-7890</li>
        <li><svg viewBox="0 0 16 16" aria-hidden="true"><path d="M1 3h14v10H1z M1 3l7 6 7-6" stroke="#0f8d45" stroke-width="1.2"/></svg>yourdomain.com</li>
        <li><svg viewBox="0 0 16 16" aria-hidden="true"><path d="M6 10l4-4M7 4l2-2a3 3 0 014 4l-2 2M9 12l-2 2a3 3 0 01-4-4l2-2" stroke="#fff" stroke-width="1.8" fill="none"/></svg>yourname@yourdomain.com</li>
        <li class="address"><svg viewBox="0 0 16 16" aria-hidden="true"><path d="M8 1l7 7h-2v7H10v-4H6v4H3V8H1z"/></svg><span>Street address goes here,<br>Suite #303, Alt Bldg, NY 82365</span></li>
      </ul>
    </div>
  </section>

  <section class="card card-back" aria-label="Card back">
    <div class="back-brand">
      <span class="brand-square"></span>
      <span class="brand-name">Kestrelbrook Student Accomodation</span>
    </div>
    <p class="facebook-url">facebook.com/pages/Kestrelbrook-Student-Accomodation/481920637210458</p>
  </section>
</main>
</body>
</html>
```